Design eines Hausetiketts für traditionelles Weingut
Zielgruppe
Wir das Familienweingut Brandauer in Gimbsheim/Rheinhessen sind ein traditionelles Weingut das seine Reben selbst kultiviert und die Weine auch selbst ausbaut. Wir haben jeden Schritt in der Weinherstellung selbst in der Hand und vermarkten den Wein dann an unsere Privatkunden. Unsere Kundenstruktur sieht folgendermaßen aus: Wir haben 100% Privatkunden die unseren Wein konsumieren. Da jetzt die nächste Generation in den Weinbaubetrieb einsteigt und auch Ideen hat möchten wir ein Hausetikett einführen. Im Moment haben wir noch sehr viele unterschiedliche Etiketten und kein Hausetikett. Da die Verlagsetiketten immer seltener zu unseren Vorstellungen passen, möchten wir hier auf diesem Wege ein Hausetikett anfertigen lassen. Generell möchten wir unseren Außenauftritt komplett modernisieren. Sie können sich über die Vielfalt in unserem Betrieb unter www.weingut-brandauer-beispiel.de einen Überblick verschaffen. Langfristig gesehen wollen wir aber unsere Weinkarte verkleinern.
Aufgabenstellung
Wir haben uns vor ca. 1,5 Jahren hier auf dieser Website bereits ein Logo designen lassen. Es wäre schön wenn man das Logo bei den Entwürfen für die Etiketten berücksichtigen würde. Das wäre aber KEIN MUSS. Auch wäre es gut wenn man das ,,Wein' bei unserem Namen weglassen könnte.
Das Etikett sollte aus Vorder-und Rückenetikett bestehen und edel wirken. Vorne sollte die Rebsorte und die Geschmacksangabe stehen. Der Rest sollte auf das Rückenetikett.
Das Vorderetikett sollte ein richtiger Eyecatcher sein und im Supermarkt z.B. aus vielen anderen herausstechen. Das wäre ganz wichtig.
Man kann bei den Farben unterscheiden in 3 Konzepte.
Literwein als einsteiger Wein
Dann die Gutsweine und zum Schluss die Lagenweine. Alles Farblich oder im design etwas abgesetzt.

```html
<!DOCTYPE html>
<html lang="de">
<head>
<meta charset="utf-8">
<title>Brandauer – Dornfelder Rotwein Etikett</title>
<link rel="stylesheet" href="https://fonts.googleapis.com/css2?family=Oswald:wght@700&family=Cinzel:wght@400&family=Yellowtail&display=swap">
<style>
  :root {
    --backdrop: #8f8782;
    --label-paper: #3a3a3a;
    --label-paper-dark: #262626;
    --wordmark: #1b1b1b;
    --gold-light: #f3dcae;
    --gold-mid: #c9a46b;
    --gold-deep: #9c7a45;
    --script-white: #ffffff;
    --sky: #343434;
    --hills: #4c4c4c;
    --vines: #222222;
  }
  * { margin: 0; padding: 0; box-sizing: border-box; }
  html, body {
    width: 1200px;
    height: 800px;
    overflow: hidden;
  }
  body {
    background: radial-gradient(ellipse at 40% 45%, #b3aca7 0%, var(--backdrop) 55%, #5f5754 100%);
    position: relative;
  }
  .front-label {
    position: absolute;
    left: 340px;
    top: 40px;
    width: 520px;
    height: 720px;
    background: linear-gradient(180deg, var(--label-paper) 0%, #313131 45%, var(--label-paper-dark) 100%);
    box-shadow: 0 18px 40px rgba(0, 0, 0, 0.35);
    overflow: hidden;
  }
  .landscape-photo {
    position: absolute;
    left: 0;
    right: 0;
    bottom: 0;
    height: 340px;
    background:
      linear-gradient(180deg,
        rgba(49,49,49,1) 0%,
        var(--sky) 20%,
        #5a5a5a 38%,
        var(--hills) 46%,
        #3a3a3a 58%,
        #555555 66%,
        #2c2c2c 80%,
        var(--vines) 100%);
  }
  .winery-name {
    position: absolute;
    top: 150px;
    left: 0;
    width: 100%;
    text-align: center;
    font-family: "Cinzel", serif;
    font-size: 30px;
    letter-spacing: 1px;
    color: var(--wordmark);
    text-shadow: 0 1px 0 rgba(255,255,255,0.08);
  }
  .grape-variety {
    position: absolute;
    left: 110px;
    top: 240px;
    width: 110px;
    height: 420px;
    overflow: visible;
  }
  .grape-variety text {
    font-family: "Oswald", sans-serif;
    font-weight: 700;
    font-size: 118px;
  }
  .wine-style {
    position: absolute;
    left: 150px;
    top: 300px;
    font-family: "Yellowtail", cursive;
    font-size: 70px;
    line-height: 1;
    color: var(--script-white);
    transform: rotate(6deg);
    transform-origin: left center;
  }
</style>
</head>
<body>
  <main class="front-label">
    <div class="landscape-photo" role="img" aria-label="Schwarzweißfoto einer rheinhessischen Weinberglandschaft mit Hügeln und Rebzeilen"></div>
    <div class="winery-name">BRANDAUER</div>
    <svg class="grape-variety" viewBox="0 0 110 420" role="img" aria-label="Dornfelder">
      <defs>
        <linearGradient id="gold-foil" x1="0" y1="0" x2="1" y2="0">
          <stop offset="0" stop-color="var(--gold-deep)"/>
          <stop offset="0.45" stop-color="var(--gold-light)"/>
          <stop offset="1" stop-color="var(--gold-mid)"/>
        </linearGradient>
      </defs>
      <text transform="translate(104 420) rotate(-90)" x="0" y="0" textLength="420" lengthAdjust="spacingAndGlyphs" fill="url(#gold-foil)">DORNFELDER</text>
    </svg>
    <p class="wine-style">Rotwein</p>
  </main>
</body>
</html>
```